RWT Fittings Ltd Business Cards

We need a business card with our business logo. We provide window and door installations on high-rises in west coast British Colombia, Canada.

I would like my business information and details on one side of the card, and the other side the company name with logo

Target Market(s)

General Contractors

Industry/Entity Type

Construction

Contact Information for Business Card

one side i want my company name and logo in the dark theme logo that i provided

Requirements
Must have
• Marco Peltieri, 16045518293, RWTFittings@mailbox-demo.com, 1407-5194 Linden Row Burnaby BC, V5H 2K9, Owner & Manager

```html
<!DOCTYPE html>
<html lang="en">
<head>
<meta charset="utf-8">
<title>RWT Fittings Ltd – Business Cards</title>
<link rel="stylesheet" href="https://fonts.googleapis.com/css2?family=Open+Sans:wght@400;700&display=swap">
<style>
  :root {
    --bg-light: #5a5a5a;
    --bg-dark: #151515;
    --card-black: #1b1b1b;
    --brand-blue: #29a9e1;
    --swoosh-grey: #9a9a9a;
    --text-white: #f2f2f2;
  }
  * { box-sizing: border-box; margin: 0; padding: 0; }
  html, body { width: 1200px; height: 780px; overflow: hidden; }
  body {
    background: linear-gradient(135deg, var(--bg-light) 0%, #333 50%, var(--bg-dark) 100%);
    font-family: "Open Sans", Arial, sans-serif;
    position: relative;
  }
  .card {
    position: absolute;
    top: 247px;
    width: 500px;
    height: 286px;
    overflow: hidden;
    box-shadow: 0 18px 40px rgba(0,0,0,0.55);
  }
  .card--details { left: 60px; background: var(--card-black); }
  .card--brand { left: 640px; background: var(--brand-blue); }

  .card__art { position: absolute; inset: 0; width: 100%; height: 100%; }

  .brand-mark {
    position: absolute;
    display: flex;
    align-items: center;
    gap: 8px;
    font-weight: 700;
    text-transform: uppercase;
    letter-spacing: 1px;
    white-space: nowrap;
  }
  .brand-mark__square { flex: none; }
  .card--details .brand-mark {
    left: 26px; top: 56px;
    color: var(--brand-blue);
    font-size: 16px;
  }
  .card--details .brand-mark__square {
    width: 18px; height: 18px; background: var(--brand-blue);
  }
  .card--brand .brand-mark {
    left: 50%; top: 50%;
    transform: translate(-50%, -50%);
    color: var(--text-white);
    font-size: 40px;
    gap: 16px;
  }
  .card--brand .brand-mark__square {
    width: 38px; height: 38px; background: var(--text-white);
  }

  .divider {
    position: absolute;
    left: 264px; top: 38px;
    width: 1px; height: 170px;
    background: var(--brand-blue);
    transform: rotate(12deg);
    transform-origin: top left;
  }

  .contact {
    position: absolute;
    left: 282px; top: 44px;
    color: var(--text-white);
    font-size: 12px;
    line-height: 1.5;
    white-space: nowrap;
  }
  .contact__name {
    color: var(--brand-blue);
    font-size: 17px;
    font-weight: 700;
    text-transform: uppercase;
    line-height: 1.25;
  }
  .contact__role { font-size: 12.5px; margin-bottom: 8px; }
  .contact__row { display: flex; align-items: center; gap: 6px; }
  .contact__icon { width: 10px; height: 10px; flex: none; }
  .contact__address { margin-top: 8px; }
</style>
</head>
<body>

  <section class="card card--details" aria-label="Business card, contact side">
    <svg class="card__art" viewBox="0 0 500 286" aria-hidden="true">
      <path d="M0,112 C60,96 115,130 180,198 C232,252 300,286 370,286 L0,286 Z" fill="var(--brand-blue)"/>
      <path d="M26,96 C92,92 142,150 210,214 C262,262 340,282 470,286" fill="none" stroke="var(--swoosh-grey)" stroke-width="3.5"/>
    </svg>

    <div class="brand-mark">
      <span class="brand-mark__square"></span>
      <span class="brand-mark__name">RWT Fittings Ltd</span>
    </div>

    <div class="divider"></div>

    <div class="contact">
      <p class="contact__name">Marco Peltieri</p>
      <p class="contact__role">Owner &amp; Manager</p>
      <p class="contact__row">
        <svg class="contact__icon" viewBox="0 0 12 12"><path d="M3,1 L5,3.5 L4,5 C4.7,6.5 5.5,7.3 7,8 L8.5,7 L11,9 L9.5,11 C5,10.5 1.5,7 1,2.5 Z" fill="var(--brand-blue)"/></svg>
        16045518293
      </p>
      <p class="contact__row">
        <svg class="contact__icon" viewBox="0 0 12 12"><rect x="0.5" y="2" width="11" height="8" fill="var(--brand-blue)"/><path d="M0.5,2 L6,6.5 L11.5,2" fill="none" stroke="var(--card-black)" stroke-width="1"/></svg>
        RWTFittings@mailbox-demo.com
      </p>
      <p class="contact__row">
        <svg class="contact__icon" viewBox="0 0 12 12"><circle cx="6" cy="6" r="5.5" fill="var(--brand-blue)"/><path d="M0.5,6 H11.5 M6,0.5 C3,3.5 3,8.5 6,11.5 M6,0.5 C9,3.5 9,8.5 6,11.5" fill="none" stroke="var(--card-black)" stroke-width="0.8"/></svg>
        www.rwtfittings-demo.com
      </p>
      <p class="contact__address">1407-5194 Linden Row<br>Burnaby BC, V5H 2K9</p>
    </div>
  </section>

  <section class="card card--brand" aria-label="Business card, brand side">
    <div class="brand-mark">
      <span class="brand-mark__square"></span>
      <span class="brand-mark__name">RWT Fittings Ltd</span>
    </div>
  </section>

</body>
</html>
```